Vision, Mission and Culture Posters

We have written text paragraphs for our company vision and mission and need them made into a2 or a3 sized posters using our logo for inspiration for colour. Our company culture has 10 paragraphs and we'd like this to be a single poster of a2 or a1. Each poster should have the logo on and share common design. It's not a complex job really.

Industry/Entity Type

It Company

Requirements
Nice to have
• These will be going up on our office wall so need to be clear to read from a distance and look professional but also not stodgy.

```html
<!DOCTYPE html>
<html lang="en">
<head>
<meta charset="utf-8">
<title>Bayline Lot Hire — Mission</title>
<link rel="stylesheet" href="https://fonts.googleapis.com/css2?family=Anton&family=Alfa+Slab+One&family=Josefin+Slab:wght@100&family=Arimo:wght@400;700&display=swap">
<style>
  :root {
    --brand-yellow: #fff200;
    --brand-red: #d4242c;
    --ink: #111111;
    --paper: #f6f5f0;
    --paper-edge: #f3efc4;
  }
  html, body {
    margin: 0;
    padding: 0;
    width: 1200px;
    height: 849px;
    overflow: hidden;
    background: var(--paper);
  }
  .poster {
    display: block;
    width: 1200px;
    height: 849px;
  }
  .brand-name { font-family: "Arimo", Arial, sans-serif; font-weight: 700; fill: var(--ink); }
  .badge-title { font-family: "Anton", "Impact", sans-serif; fill: var(--brand-yellow); }
  .lead-in { font-family: "Josefin Slab", Georgia, serif; font-weight: 100; fill: var(--ink); }
  .verb { font-family: "Anton", "Impact", sans-serif; fill: var(--ink); }
  .headline-slab { font-family: "Alfa Slab One", Georgia, serif; fill: var(--brand-yellow); stroke: var(--ink); stroke-width: 3; paint-order: stroke fill; }
  .headline-bold { font-family: "Anton", "Impact", sans-serif; fill: var(--brand-red); }
  .belief { font-family: "Alfa Slab One", Georgia, serif; fill: var(--ink); }
  .belief .accent { fill: var(--brand-red); }
  .approach { font-family: "Arimo", Arial, sans-serif; font-weight: 400; fill: #222222; }
</style>
</head>
<body>
<svg class="poster" viewBox="0 0 1200 849" xmlns="http://www.w3.org/2000/svg">
  <defs>
    <radialGradient id="paper-glow" cx="50%" cy="55%" r="70%">
      <stop offset="0.55" stop-color="var(--paper)"/>
      <stop offset="1" stop-color="var(--paper-edge)"/>
    </radialGradient>
  </defs>

  <!-- background -->
  <rect class="backdrop" width="1200" height="849" fill="url(#paper-glow)"/>

  <!-- top yellow band -->
  <path class="top-band" d="M0 0 H1200 V68 C1150 100 1110 150 1060 164 C1040 168 1030 168 1000 167 L0 153 Z" fill="var(--brand-yellow)"/>
  <path class="top-band-edge" d="M0 153 L1000 167 C1030 168 1040 168 1060 164 C1110 150 1150 100 1200 68" fill="none" stroke="var(--ink)" stroke-width="3"/>

  <!-- brand name -->
  <g class="brand">
    <rect x="108" y="68" width="28" height="28" fill="var(--ink)"/>
    <text class="brand-name" x="148" y="94" font-size="32">Bayline Lot Hire</text>
  </g>

  <!-- section badge -->
  <g class="section-badge">
    <rect x="541" y="28" width="386" height="109" rx="12" fill="var(--ink)"/>
    <text class="badge-title" x="734" y="126" font-size="112" text-anchor="middle" textLength="340" lengthAdjust="spacingAndGlyphs">MISSION</text>
  </g>

  <!-- headline -->
  <g class="headline">
    <text class="lead-in" x="71" y="278" font-size="122" textLength="1048" lengthAdjust="spacingAndGlyphs">OUR MISSION IS TO</text>
    <text class="verb" transform="translate(157 541) rotate(-90)" x="0" y="0" font-size="96" textLength="254" lengthAdjust="spacingAndGlyphs">ACHIEVE</text>
    <text class="headline-slab" x="175" y="398" font-size="128" textLength="950" lengthAdjust="spacingAndGlyphs">GREAT CUSTOMER</text>
    <text class="headline-bold" x="173" y="541" font-size="160" textLength="950" lengthAdjust="spacingAndGlyphs">SATISFACTION</text>
  </g>

  <!-- belief statement -->
  <g class="belief-box">
    <rect x="66" y="555" width="1064" height="131" fill="none" stroke="var(--ink)" stroke-width="3"/>
    <text class="belief" x="77" y="593" font-size="29" textLength="1043" lengthAdjust="spacingAndGlyphs">WE BELIEVE OUR PATH TO ACHIEVING THIS COMES THROUGH</text>
    <text class="belief" x="77" y="633" font-size="29" textLength="1043" lengthAdjust="spacingAndGlyphs">GIVING A <tspan class="accent">SIMPLE YET THOROUGH AND FRIENDLY SERVICE</tspan> TO</text>
    <text class="belief" x="77" y="673" font-size="29" textLength="1043" lengthAdjust="spacingAndGlyphs">OUR CUSTOMERS WITHOUT UNNECESSARY COMPLICATION.</text>
  </g>

  <!-- approach paragraph -->
  <g class="approach-text">
    <text class="approach" x="597" y="720" font-size="27" text-anchor="middle" textLength="996" lengthAdjust="spacingAndGlyphs">We will achieve this through using the technology available to us, continual staff</text>
    <text class="approach" x="597" y="755" font-size="27" text-anchor="middle" textLength="1036" lengthAdjust="spacingAndGlyphs">training and development, regular refinement of our practices and processes along</text>
    <text class="approach" x="597" y="790" font-size="27" text-anchor="middle" textLength="943" lengthAdjust="spacingAndGlyphs">with commitment to our roles and the foundations for building our success.</text>
  </g>

  <!-- bottom red band -->
  <path class="bottom-band" d="M0 828 L1130 824 C1160 822 1175 812 1200 812 V849 H0 Z" fill="var(--brand-red)"/>
  <path class="bottom-band-edge" d="M0 828 L1130 824 C1160 822 1175 812 1200 812" fill="none" stroke="var(--ink)" stroke-width="3"/>
</svg>
</body>
</html>
```